Golf Brochure + Business Card Design Project – Kestrel Fitness.

Task Description

We are looking for a premium tri-fold brochure (8.5x11 letter, folded) plus a new business card design for Kestrel Fitness. Both need to look polished, elegant, and professional — something that would feel at home in a golf club environment.

Brochure Scope:
• Tri-fold brochure promoting our new golf-specific services
• Incorporate brand colors: deep hunter green, cream, and gold accents
• Clean, modern typography (professional, not playful)
• Layout will follow the copy provided (final copy attached, no rewriting needed)
• Imagery: mature golfers (50+), golf lifestyle shots, no generic stocky images
• Include QR code placement linking to booking page
• Deliverables: print-ready PDF with bleed/crop (CMYK), high-res PDF (digital), and source file (InDesign or Illustrator)

Business Card Scope:
• Front + back design
• Consistent with brand colors and fonts
• Space for name, title, phone, email, and website
• Deliverables: print-ready PDF with bleed/crop (CMYK) + source file (AI or InDesign)
• If possible, provide editable template for future staff cards

Timeline:
• First draft within 5–7 days
• 2 rounds of revisions included

Budget:
$300 USD (total for both brochure + business card)

I’ll provide finalized copy if you accept the project.
Project description (paste this whole block in that box)

We need a premium tri-fold brochure (8.5”×11” letter, folded) and a new business card design for Kestrel Fitness. This will be presented to golf course managers and members, so the look must be elegant, restrained, and country-club-classy.

Scope — Brochure
• Format: Tri-fold, 8.5”×11”. Please set 0.125” bleed on all sides and keep critical text ≥0.125–0.25” inside the trim.
• Purpose: Promote Kestrel Fitness’ golf-specific services for adults 50+.
• Copy: We will provide finalized copy in a Word doc after acceptance. No rewriting needed — please focus on layout and polish.
• Imagery (required):
• Golf-first images (ball on tee/green, mature golfers mid-swing, and golf course landscapes at golden hour).
• 1–2 real Kestrel Fitness gym photos on inside panels (trainer with client doing golf-relevant movement: stretch, rotation, balance).
• Visual style: Premium, quiet, lots of white/negative space, balanced grids; no clutter.
• Brand colors (required): Hunter Green #0C2E1F, Gold #CBA135, Cream #F5F2EB. Convert for CMYK print while preserving the look.
• Typography: Clean, legible serif + sans pairing (e.g., modern serif for headlines, humanist/neo-grotesk sans for body). You may propose suitable professional fonts; avoid playful/novelty fonts.
• Elements to include:
• Our logo (we will upload).
• QR code placement to booking page (we will supply the URL / QR asset).
• Simple icon treatment for the three complimentary options (Strength & Mobility, Stretch Therapy, Vitrascan + Assessment).
• Deliverables:
• Print-ready PDF (CMYK, with bleed & crop marks, PDF/X-1a or PDF/X-4)
• High-res digital PDF (no bleed)
• Source file (InDesign or Illustrator) + packaged fonts/links or outlined type as appropriate.

Scope — Business Card
• Size: 3.5”×2” (US standard) with 0.125” bleed; keep text ≥0.125” from trim.
• Front/back design; consistent with brochure branding.
• Fields: Name, Title, Phone, Email, Website, Address; optional small QR on back.
• Deliverables: Print-ready PDF (CMYK, bleed & crops) + Source file (AI/INDD). Provide an editable template for staff names.

Process & Timing
• Initial concept for brochure + card within 5–7 days of acceptance.
• 2 rounds of revisions included.
• Please start with a clean layout concept using placeholder images/text blocks; we’ll drop in final copy/assets immediately after acceptance.

Stock & Licensing
• You may propose stock images that fit the brief (we’re fine approving Pixelgrove or equivalent). Please note any license fees separately if needed.

Usage Rights
• We require full usage rights to the final designs for print & digital.

Target Market(s)

Golfers 50+ in Victoria, BC: quality-oriented, health-conscious, want to play longer, stronger, and pain-free. Country-club aesthetic; expect polished, professional materials.

Industry/Entity Type

Health & Fitness — Golf Performance / Longevity Studio

Font styles to use
Serif
Sans Serif

Requirements
Must have
• • Golf-first imagery + 1–2 real Kestrel Fitness photos inside. • Brand colors: #0C2E1F (Hunter Green), #CBA135 (Gold), #F5F2EB (Cream). • Premium, restrained layout; ample negative space; no clutter. • Clean professional serif + sans type pairing; highly legible. • Space for logo and QR code (booking). • Correct print specs (bleed, crops, CMYK). • Deliverables: print-ready PDFs (brochure + card), digital PDF, source files.
Nice to have
• • Subtle texture or grain in backgrounds (very light) to add sophistication. • A second brochure cover variation (ball on tee vs. course landscape) at concept stage.
Should not have
• • Cheesy/posed “stocky” groups; overly young models; beer/alcohol imagery. • Over-saturated greens/blues; gimmicky gradients or clip art. • Generic fitness/bodybuilding shots unrelated to golf performance.

```html
<!DOCTYPE html>
<html lang="en">
<head>
<meta charset="utf-8">
<title>Kestrel Fitness – Business Card</title>
<link rel="stylesheet" href="https://fonts.googleapis.com/css2?family=Outfit:wght@400;500;600;700&display=swap">
<style>
  :root {
    --backdrop: #ababab;
    --cream: #fefbd2;
    --hunter: #0d3538;
    --ink: #0e3437;
    --gold: #c9a045;
    --gold-soft: #b8913c;
  }
  * { box-sizing: border-box; margin: 0; padding: 0; }
  html, body {
    width: 1093px;
    height: 1200px;
    overflow: hidden;
    background: var(--backdrop);
    font-family: "Outfit", sans-serif;
  }
  .canvas { position: relative; width: 1093px; height: 1200px; }

  .card {
    position: absolute;
    left: 265px;
    width: 580px;
    height: 356px;
    border-radius: 27px;
    overflow: hidden;
  }

  /* Front */
  .card-front {
    top: 226px;
    background: var(--cream);
    color: var(--ink);
    text-align: center;
  }
  .holder-name {
    position: absolute; left: 0; right: 0; top: 72px;
    font-size: 30px; font-weight: 600; letter-spacing: 0.2px;
  }
  .holder-title {
    position: absolute; left: 0; right: 0; top: 112px;
    font-size: 20px; font-weight: 500;
  }
  .contact-divider {
    position: absolute; left: 174px; width: 232px; top: 155px; height: 22px;
    display: flex; align-items: center; gap: 6px;
  }
  .contact-divider .rule { flex: 1; height: 1px; background: var(--ink); opacity: .7; }
  .contact-divider .icon-dot {
    width: 22px; height: 22px; border-radius: 50%;
    background: var(--hunter);
    display: flex; align-items: center; justify-content: center;
  }
  .contact-divider .icon-dot svg { width: 12px; height: 12px; }
  .contact-divider .rule:first-child { margin-right: 2px; }
  .contact-divider .rule:last-child { margin-left: 2px; }
  .contact-list {
    position: absolute; left: 0; right: 0; top: 189px;
    list-style: none;
    font-size: 21px; font-weight: 500; line-height: 32.5px;
  }

  /* Back */
  .card-back {
    top: 621px;
    background: var(--hunter);
    color: var(--gold);
    text-align: center;
  }
  .brand-ring {
    position: absolute; left: 245px; top: 56px;
    width: 90px; height: 90px; border-radius: 50%;
    border: 2px solid var(--gold);
  }
  .brand-name {
    position: absolute; left: 0; right: 0; top: 168px;
    font-size: 30px; font-weight: 600; letter-spacing: 4px;
    text-transform: uppercase;
  }
  .tagline {
    position: absolute; left: 0; right: 0; top: 296px;
    font-size: 17px; font-weight: 600; letter-spacing: 0.3px;
  }
</style>
</head>
<body>
<main class="canvas">

  <section class="card card-front" aria-label="Business card front">
    <h1 class="holder-name">MAREN-ELISE WHITFORD</h1>
    <p class="holder-title">Owner | Kestrel Fitness</p>

    <div class="contact-divider">
      <span class="rule"></span>
      <span class="icon-dot" aria-label="Phone">
        <svg viewBox="0 0 24 24" fill="none" stroke="#fefbd2" stroke-width="2.2" stroke-linecap="round" stroke-linejoin="round">
          <path d="M22 16.9v3a2 2 0 0 1-2.2 2 19.8 19.8 0 0 1-8.6-3.1 19.5 19.5 0 0 1-6-6A19.8 19.8 0 0 1 2.1 4.2 2 2 0 0 1 4.1 2h3a2 2 0 0 1 2 1.7c.1.9.4 1.8.7 2.7a2 2 0 0 1-.5 2.1L8 9.8a16 16 0 0 0 6 6l1.3-1.3a2 2 0 0 1 2.1-.4c.9.3 1.8.6 2.7.7a2 2 0 0 1 1.7 2z"/>
        </svg>
      </span>
      <span class="icon-dot" aria-label="Email">
        <svg viewBox="0 0 24 24" fill="none" stroke="#fefbd2" stroke-width="2.2" stroke-linejoin="round">
          <rect x="2" y="5" width="20" height="14" rx="1.5"/>
          <path d="M2 6l10 7 10-7"/>
        </svg>
      </span>
      <span class="icon-dot" aria-label="Website">
        <svg viewBox="0 0 24 24" fill="none" stroke="#fefbd2" stroke-width="2">
          <circle cx="12" cy="12" r="10"/>
          <path d="M2 12h20M12 2c3 3 3 17 0 20M12 2c-3 3-3 17 0 20"/>
        </svg>
      </span>
      <span class="rule"></span>
    </div>

    <ul class="contact-list">
      <li class="contact-phone">250-555-0147</li>
      <li class="contact-email">maren-elise@kestrelfitness.biz</li>
      <li class="contact-web">kestrelfitnessvictoria.com</li>
    </ul>
  </section>

  <section class="card card-back" aria-label="Business card back">
    <span class="brand-ring" aria-hidden="true"></span>
    <p class="brand-name">Kestrel Fitness</p>
    <p class="tagline">STRENGTH • MOBILITY • LONGEVITY</p>
  </section>

</main>
</body>
</html>
```